Marrowind - IT Consultancy Website

Our company is called Marrowind and our purpose is to help companies sustainably embrace and reap the benefits of cloud platforms, through transforming practices, skills and technology using DevOps and Security practices such that they are able to automate, manage and secure their cloud platforms to deliver product to market with increasing velocity.

To get our business started I require a website that will model the typical layout of an IT consultancy services company to an Australian Market. There are many examples of such a site, here are some of them. We would like a landing page and then a few simple menu options (About, Blog, Services etc..) to additional content

http://pelvo.com.au/
http://www.brisket.com.au/
http://www.tandu.com.au/

I require the site to be created with a separate CSS file that maintains the colour palette. This is a very important requirement, I want to be able to change the colours employed in the site in a single location and not have to scan through multiple files to replace the codes.

The website must be built using static content as it will not be hosted on a web server but instead in QNT using S3 and CloudFront CDN. Therefore please stick to HTML, JavaScript, CSS and other static file formats. The website needs to be response, smooth and reactive. It should render on desktop, mobile and tablet and feature smooth scrolling, transitions and fade in's.

The website should give the customer confidence that they are dealing with a highly professional IT services company, focused strongly on cloud (QNT, Vantrel Skyline, Horvik Vapor etc..), motivated by beautiful and fluid design.

In order to make this simpler for you, the designer, I have already purchased this template from https://skinmarketly.com/theme/the-venture-allround-template-KX7Q41093 and uploaded it. Feel free to use this template if you choose (note that it makes use of a separate color palette which is a key requirement) or use one of your own choosing. If you do use this template ensure that it does not look too much like "another bootstrap site" therefore use the layout and widgets but make the site look fresh and original too.
Obviously you must delete all trace of the bootstrap package once the project has completed if you do use it

Target Market(s)

Corporate and medium enterprise businesses

Industry/Entity Type

Information Technology

Coding

Coded - Design and coding required

Number of Pages Required

4 page

Font styles to use
Sans Serif

Colors
abd036
33a6d7

Requirements
Must have
• The website should give the customer confidence that they are dealing with a highly professional IT services company, focused strongly on cloud (QNT, Vantrel Skyline, Horvik Vapor etc..), motivated by beautiful and fluid design. Our company name is Marrowind, the site needs to pay homage to the themes of fluidity and logic
• Along with About Us, Services and a Blog page could I also get social logo's included too
Nice to have
• The website must be built using static content as it will not be hosted on a web server but instead in QNT using S3 and CloudFront CDN. Therefore please stick to HTML, JavaScript, CSS and other static file formats. The website needs to be response, smooth and reactive. It should render on desktop, mobile and tablet and feature smooth scrolling, transitions and fade in's.
Should not have
• Lurid colours, or too much animations. The design must "flow"

```html
<!DOCTYPE html>
<html lang="en">
<head>
<meta charset="utf-8">
<title>Marrowind IT Consultancy</title>
<link rel="stylesheet" href="https://fonts.googleapis.com/css2?family=Roboto:wght@400;500;700&family=Raleway:wght@400;500;600&display=swap">
<style>
:root{
  --blue:#1ea5d8;
  --blue-deep:#1590c0;
  --dark:#2e2e2e;
  --darker:#252525;
  --ink:#2b2b2b;
  --muted:#666;
  --line:#d9d9d9;
  --white:#fff;
  --head:"Roboto",Arial,sans-serif;
  --body:"Raleway",Arial,sans-serif;
}
*{box-sizing:border-box;margin:0;padding:0}
html,body{width:1200px;height:3186px;overflow:hidden}
body{font-family:var(--body);color:var(--ink);background:var(--white);position:relative}
section,header,footer{position:absolute;left:0;width:1200px}
.abs{position:absolute}

/* header */
.site-header{top:0;height:153px;border-top:4px solid var(--blue);background:var(--white)}
.brand{left:100px;top:40px;display:flex;align-items:center;gap:14px}
.brand-mark{width:48px;height:48px;background:var(--blue);border-radius:6px}
.brand-name{font-family:var(--head);font-weight:500;font-size:27px;line-height:32px;color:var(--ink)}
.social-top{left:545px;top:32px;display:flex;gap:10px}
.social-top span{width:36px;height:36px;border-radius:50%;background:#3b5998}
.social-top span:nth-child(2){background:#3fa9e6}
.social-top span:nth-child(3){background:#3d6b8f}
.social-top span:nth-child(4){background:#c92228}
.contact-top{top:32px;display:flex;align-items:center;gap:10px;font-family:var(--head);font-size:17px}
.contact-top .dot{width:36px;height:36px;border-radius:50%;display:flex;align-items:center;justify-content:center}
.mail{left:735px;color:var(--blue)}
.mail .dot{background:var(--blue)}
.phone{left:935px;color:var(--ink)}
.phone .dot{background:var(--dark)}
.main-nav{left:510px;top:108px;display:flex;gap:0;font-family:var(--head);font-size:16px}
.main-nav a{color:var(--ink);text-decoration:none;padding:4px 0 18px;margin-right:42px;position:relative}
.main-nav a.active{color:var(--blue)}
.main-nav a.active::after{content:"";position:absolute;left:0;right:0;bottom:0;height:3px;background:var(--blue)}

/* hero */
.hero{top:153px;height:527px;background:linear-gradient(135deg,#3a3a3a,#1e1e1e 55%,#2d2d2d)}
.hero-title{top:96px;width:100%;text-align:center;font-family:var(--head);font-weight:500;font-size:50px;color:var(--white)}
.hero-sub{top:178px;width:100%;text-align:center;font-family:var(--head);font-size:20px;color:var(--white)}
.btn-ghost{border:2px solid var(--white);border-radius:24px;color:var(--white);font-family:var(--head);font-size:17px;display:flex;align-items:center;justify-content:center}
.hero .btn-ghost{left:502px;top:242px;width:196px;height:48px}
.slider-dots{left:1150px;top:156px;display:flex;flex-direction:column;gap:12px}
.slider-dots span{width:15px;height:15px;border-radius:50%;border:2px solid var(--white)}
.slider-dots span:first-child{background:var(--blue);border-color:var(--blue)}
.tile{top:372px;height:127px;width:320px;display:flex;align-items:center;gap:18px;padding:0 20px;color:var(--white)}
.tile.blue{background:rgba(30,165,216,.8)}
.tile.dark{background:rgba(25,25,25,.85)}
.tile h3{font-family:var(--head);font-weight:700;font-size:16px;margin-bottom:8px}
.tile p{font-family:var(--head);font-size:14px;line-height:21px}
.tile svg{flex:none}

/* band */
.offer-band{top:680px;height:85px;background:var(--dark);border-top:3px solid var(--blue);border-bottom:3px solid var(--blue)}
.offer-band p{left:100px;top:26px;font-family:var(--head);font-weight:500;font-size:19px;color:var(--white)}
.btn-solid{background:var(--blue);color:var(--white);font-family:var(--head);font-weight:500;font-size:16px;display:flex;align-items:center;justify-content:center;border-radius:3px}
.offer-band .btn-solid{left:918px;top:17px;width:154px;height:46px}

/* features */
.features{top:765px;height:543px}
.screen-monitor{left:127px;top:57px;width:325px;height:406px;border-radius:12px;background:linear-gradient(180deg,#2a2a2a 0,#2a2a2a 70%,#cfcfcf 70%,#eee)}
.sec-title{font-family:var(--head);font-size:27px;font-weight:400;color:var(--ink)}
.sec-title b{color:var(--blue);font-weight:500}
.lead{font-size:14px;line-height:26px;color:var(--muted)}
.features .sec-title{left:540px;top:72px}
.features .lead{left:540px;top:120px;width:560px}
.feature-list{left:540px;top:198px;width:552px}
.feature-item{display:flex;gap:24px;height:111px;border-bottom:1px solid var(--line);padding-top:10px}
.feature-item:last-child{border-bottom:none}
.feature-item h4{font-size:17px;font-weight:500;margin-bottom:10px}
.feature-item p{font-size:13px;line-height:26px;color:var(--muted)}
.feature-item svg{flex:none;margin-top:4px}

/* why */
.why{top:1308px;height:595px;background:linear-gradient(180deg,#3a3d40,#2b2d30);color:var(--white)}
.why .sec-title{width:100%;text-align:center;top:40px;color:var(--white);font-weight:500;font-size:29px}
.why .lead{top:96px;left:210px;width:780px;text-align:center;color:#eee}
.provider{top:190px;width:340px;text-align:center}
.provider .disc{width:144px;height:144px;border-radius:50%;background:var(--blue);margin:0 auto}
.provider h3{font-family:var(--head);font-weight:400;font-size:23px;margin:26px 0 16px}
.provider p{font-size:13px;line-height:26px;color:#eee;padding:0 30px}
.provider .btn-ghost{width:140px;height:46px;margin:28px auto 0;font-size:14px}

/* amazing */
.amazing{top:1903px;height:544px}
.amazing .sec-title{right:542px;top:52px;text-align:right}
.amazing .lead{left:100px;top:100px;width:560px;text-align:right}
.amazing-list{left:100px;top:176px;width:476px}
.amazing-item{height:111px;border-bottom:1px solid var(--line);text-align:right;padding-top:10px}
.amazing-item:last-child{border-bottom:none}
.amazing-item h4{font-size:17px;font-weight:500;margin-bottom:10px}
.amazing-item p{font-size:13px;line-height:26px;color:var(--muted)}
.amazing-icons{left:608px;top:190px;display:flex;flex-direction:column;gap:72px}
.screen-phone{left:803px;top:47px;width:225px;height:433px;border-radius:24px;background:linear-gradient(180deg,#2a2a2a,#3c3c3c)}

/* testimonials */
.testimonials{top:2447px;height:234px;background:var(--blue);color:var(--white)}
.portrait{left:113px;top:43px;width:140px;height:140px;border-radius:50%;border:4px solid var(--white);background:linear-gradient(160deg,#e9c9a8,#b98c6a)}
.quote-badge{left:206px;top:142px;width:46px;height:46px;border-radius:50%;background:var(--blue-deep);border:3px solid var(--white)}
.testimonials h2{left:310px;top:50px;font-family:var(--head);font-weight:500;font-size:27px}
.testimonials blockquote{left:310px;top:104px;width:770px;font-size:14px;line-height:26px}
.testimonials cite{left:310px;top:166px;font-style:normal;font-size:13px;font-weight:600}
.t-arrows{left:1042px;top:52px;display:flex;gap:12px}
.t-arrows span{width:18px;height:18px;border-radius:50%;background:rgba(255,255,255,.8)}

/* footer */
.site-footer{top:2681px;height:446px;background:var(--dark);color:var(--white)}
.footer-brand{left:478px;top:44px;display:flex;align-items:center;gap:14px}
.footer-brand .brand-mark{background:var(--white)}
.footer-brand .brand-name{color:var(--white)}
.site-footer .about{left:225px;top:144px;width:750px;text-align:center;font-size:13px;line-height:28px;color:#ddd}
.footer-contacts{left:255px;top:228px;display:flex;gap:70px;font-family:var(--head);font-size:15px;font-weight:500}
.footer-contacts div{display:flex;align-items:center;gap:14px}
.footer-contacts .ring{width:42px;height:42px;border-radius:50%;border:2px solid var(--white);display:flex;align-items:center;justify-content:center}
.footer-rule{left:100px;top:314px;width:1000px;height:1px;background:#666}
.social-footer{left:432px;top:358px;display:flex;gap:12px}
.social-footer span{width:46px;height:46px;border-radius:50%;border:2px solid var(--white)}
.copyright{left:0;top:3127px;width:1200px;height:59px;background:var(--blue);color:var(--white);font-family:var(--head);font-size:14px;display:flex;align-items:center;justify-content:center;white-space:nowrap}
</style>
</head>
<body>

<header class="site-header">
  <div class="brand abs"><span class="brand-mark"></span><span class="brand-name">Marrowind<br>IT Consultancy</span></div>
  <div class="social-top abs" aria-label="Social links"><span></span><span></span><span></span><span></span></div>
  <div class="contact-top mail abs"><span class="dot"><svg width="18" height="14" viewBox="0 0 18 14"><rect x="1" y="1" width="16" height="12" fill="none" stroke="#fff" stroke-width="2"/><path d="M1 1l8 6 8-6" fill="none" stroke="#fff" stroke-width="2"/></svg></span>info@marrowind.in</div>
  <div class="contact-top phone abs"><span class="dot"><svg width="16" height="16" viewBox="0 0 16 16"><path d="M3 1l3 3-2 2c1 2 3 4 5 5l2-2 3 3-2 2C7 14 2 9 1 3z" fill="#fff"/></svg></span>1800 4710 2286</div>
  <nav class="main-nav abs"><a class="active">Home</a><a>About Us</a><a>Features</a><a>Our Services</a><a>Blog</a><a>Contact Us</a></nav>
</header>

<section class="hero" role="img" aria-label="Photo of a desk with laptop, notebook and tablet">
  <h1 class="hero-title abs">IT SERVICES COMPANY</h1>
  <p class="hero-sub abs">We help companies sustainably embrace and reap the benefits of cloud platforms</p>
  <span class="btn-ghost abs">LEARN WITH US</span>
  <div class="slider-dots abs"><span></span><span></span><span></span><span></span><span></span></div>
  <div class="tile blue abs" style="left:100px">
    <svg width="54" height="54" viewBox="0 0 54 54" fill="none" stroke="#fff" stroke-width="2.5"><path d="M12 6h20l8 8v22H12z"/><rect x="6" y="32" width="42" height="14"/></svg>
    <div><h3>CLEAN CODE &amp; DESIGN</h3><p>Voluptatem ad provident non repudiandae beatae.</p></div>
  </div>
  <div class="tile dark abs" style="left:442px">
    <svg width="54" height="54" viewBox="0 0 54 54" fill="none" stroke="#fff" stroke-width="2.5"><rect x="16" y="6" width="32" height="24"/><circle cx="10" cy="40" r="5"/><circle cx="24" cy="44" r="5"/><circle cx="38" cy="44" r="5"/></svg>
    <div><h3>EXTREMELY FLEXIBLE</h3><p>Voluptatem ad provident non repudiandae beatae.</p></div>
  </div>
  <div class="tile blue abs" style="left:780px">
    <svg width="54" height="54" viewBox="0 0 54 54" fill="none" stroke="#fff" stroke-width="2.5"><rect x="6" y="8" width="42" height="30"/><path d="M20 46h14M27 38v8"/></svg>
    <div><h3>LATEST TECHNOLOGIES</h3><p>Voluptatem ad provident non repudiandae beatae.</p></div>
  </div>
</section>

<section class="offer-band">
  <p class="abs">WE OFFER MORE POSSIBILITIES TO MEET YOUR EVERY NEED</p>
  <span class="btn-solid abs">Learn More</span>
</section>

<section class="features">
  <div class="screen-monitor abs" role="img" aria-label="Desktop monitor showing the website"></div>
  <h2 class="sec-title abs">CORE <b>FEATURES</b></h2>
  <p class="lead abs">Lorem ipsum dolor sit amet, consectetur adipisicing elit. Non tempore mollitia sed, tem poribus, quaerat recusandae!</p>
  <div class="feature-list abs">
    <div class="feature-item">
      <svg width="46" height="40" viewBox="0 0 46 40" fill="none" stroke="#1ea5d8" stroke-width="2.5"><rect x="3" y="3" width="40" height="26"/><path d="M16 37h14M23 29v8"/></svg>
      <div><h4>Benefits of cloud platforms</h4><p>Voluptatem ad provident non repudiandae beatae cupiditate amet reiciendis<br>lorem dolor consectetur.</p></div>
    </div>
    <div class="feature-item">
      <svg width="46" height="40" viewBox="0 0 46 40" fill="none" stroke="#1ea5d8" stroke-width="2.5"><path d="M10 3h18l6 6v16H10z"/><rect x="4" y="24" width="38" height="13"/></svg>
      <div><h4>Through transforming practices</h4><p>Voluptatem ad provident non repudiandae beatae cupiditate amet reiciendis<br>lorem dolor consectetur.</p></div>
    </div>
    <div class="feature-item">
      <svg width="46" height="40" viewBox="0 0 46 40" fill="none" stroke="#1ea5d8" stroke-width="2.5"><rect x="16" y="3" width="26" height="20"/><circle cx="9" cy="30" r="5"/><circle cx="21" cy="33" r="5"/><circle cx="33" cy="33" r="5"/></svg>
      <div><h4>Skills and technology</h4><p>Voluptatem ad provident non repudiandae beatae cupiditate amet reiciendis<br>lorem dolor consectetur.</p></div>
    </div>
  </div>
</section>

<section class="why" role="img" aria-label="Photo of a team in a meeting room, darkened">
  <h2 class="sec-title abs">WHY CHOOSE US?</h2>
  <p class="lead abs">Lorem ipsum dolor sit amet, consectetur adipisicing elit. Numquam voluptas facere vero ex tempora saepe perspiciatis ducimus sequi animi.</p>
  <div class="provider abs" style="left:89px"><div class="disc"></div><h3>Cloud QNT</h3><p>Voluptatem ad provident non repudiandae beatae cupiditate amet reiciendis lorem ipsum dolor sit amet, consectetur.</p><div class="btn-ghost">Read More &gt;&gt;</div></div>
  <div class="provider abs" style="left:429px"><div class="disc"></div><h3>Vantrel Skyline</h3><p>Voluptatem ad provident non repudiandae beatae cupiditate amet reiciendis lorem ipsum dolor sit amet, consectetur.</p><div class="btn-ghost">Read More &gt;&gt;</div></div>
  <div class="provider abs" style="left:779px"><div class="disc"></div><h3>Horvik Vapor</h3><p>Voluptatem ad provident non repudiandae beatae cupiditate amet reiciendis lorem ipsum dolor sit amet, consectetur.</p><div class="btn-ghost">Read More &gt;&gt;</div></div>
</section>

<section class="amazing">
  <h2 class="sec-title abs">SIMPLY <b>AMAZING</b></h2>
  <p class="lead abs">Lorem ipsum dolor sit amet, consectetur adipisicing elit. Non tempore mollitia sed, tem poribus, quaerat recusandae!</p>
  <div class="amazing-list abs">
    <div class="amazing-item"><h4>Benefits of cloud platforms</h4><p>Voluptatem ad provident non repudiandae beatae cupiditate amet reiciendis<br>lorem dolor consectetur.</p></div>
    <div class="amazing-item"><h4>Through transforming practices</h4><p>Voluptatem ad provident non repudiandae beatae cupiditate amet reiciendis<br>lorem dolor consectetur.</p></div>
    <div class="amazing-item"><h4>Skills and technology</h4><p>Voluptatem ad provident non repudiandae beatae cupiditate amet reiciendis<br>lorem dolor consectetur.</p></div>
  </div>
  <div class="amazing-icons abs">
    <svg width="46" height="40" viewBox="0 0 46 40" fill="none" stroke="#1ea5d8" stroke-width="2.5"><rect x="3" y="3" width="40" height="26"/><path d="M16 37h14M23 29v8"/></svg>
    <svg width="46" height="40" viewBox="0 0 46 40" fill="none" stroke="#1ea5d8" stroke-width="2.5"><path d="M10 3h18l6 6v16H10z"/><rect x="4" y="24" width="38" height="13"/></svg>
    <svg width="46" height="40" viewBox="0 0 46 40" fill="none" stroke="#1ea5d8" stroke-width="2.5"><rect x="16" y="3" width="26" height="20"/><circle cx="9" cy="30" r="5"/><circle cx="21" cy="33" r="5"/><circle cx="33" cy="33" r="5"/></svg>
  </div>
  <div class="screen-phone abs" role="img" aria-label="Mobile phone showing the website"></div>
</section>

<section class="testimonials">
  <div class="portrait abs" role="img" aria-label="Client portrait"></div>
  <span class="quote-badge abs"></span>
  <h2 class="abs">CLIENT TESTIMONIALS</h2>
  <blockquote class="abs">"Lorem ipsum dolor sit amet, consectetuer adipiscing elit. Sed posuere interdum sem. Quisque ligula eros ullamcorper quis, lacinia quis facilisis sed sapien. Mauris varius diam vitae arcu."</blockquote>
  <cite class="abs">- Name, company, industry</cite>
  <div class="t-arrows abs"><span></span><span></span></div>
</section>

<footer class="site-footer">
  <div class="footer-brand abs"><span class="brand-mark"></span><span class="brand-name">Marrowind<br>IT Consultancy</span></div>
  <p class="about abs">Lorem ipsum dolor sit amet, consectetur adipisicing elit. Necessitatibus illo vel dolorum soluta consectetur doloribus sit. Delectus non tenetur odit dicta vitae debitis suscipit doloribus.</p>
  <div class="footer-contacts abs">
    <div><span class="ring"><svg width="14" height="18" viewBox="0 0 14 18"><path d="M7 1a6 6 0 0 1 6 6c0 4-6 10-6 10S1 11 1 7a6 6 0 0 1 6-6z" fill="none" stroke="#fff" stroke-width="2"/><circle cx="7" cy="7" r="2" fill="#fff"/></svg></span>Twelve Harbour Lane, 54100</div>
    <div><span class="ring"><svg width="16" height="16" viewBox="0 0 16 16"><path d="M3 1l3 3-2 2c1 2 3 4 5 5l2-2 3 3-2 2C7 14 2 9 1 3z" fill="none" stroke="#fff" stroke-width="1.6"/></svg></span>1800 4710 2286</div>
    <div><span class="ring"><svg width="18" height="14" viewBox="0 0 18 14"><rect x="1" y="1" width="16" height="12" fill="none" stroke="#fff" stroke-width="2"/><path d="M1 1l8 6 8-6" fill="none" stroke="#fff" stroke-width="2"/></svg></span>info@marrowind.in</div>
  </div>
  <div class="footer-rule abs"></div>
  <div class="social-footer abs" aria-label="Social links"><span></span><span></span><span></span><span></span><span></span><span></span></div>
</footer>

<div class="copyright abs">© 2016 Marrowind IT Consultancy. All Rights Reserved.</div>

</body>
</html>
```